Clean & Inspiring Web Design Project

Brindlecove Object Works, LLC (also known as T7-Works) is a company which provides 3D printing services and products. The emphasis is on making these products and services available to the mass-market - customers and users who may or may not have prior experience with 3D printing and/or rapid prototyping technologies. We are a start-up company, looking to build a clean and creativity inspiring brand - our site must encourage visitor to engage and make something. Our aim is to help take mere ideas and turn them into tangible items. We want to show a fusion of ideas (e.g. pencil sketches on graph paper) with design tools (e.g. CAD and drafting software) and rapid prototyping (e.g. Kindlo 3D printers, Stereolithography Machines, etc.). We would like the website to appear professional but at the same time easy to navigate and a good balance between text and pictures. The final design should inspire customers to nurture their ideas into real products and communicate our services to our customers. Our site should have the feel of a vibrant social community with the added benefit of tangible physical creations.

Target Market(s)

People with great ideas that need to be designed into a real product

Industry/Entity Type

Printing

Requirements
Must have
• - Website design should include 2 layouts - one for a "landing page" and one for a "content page"
- Website design must incorporate attached company logo (or derivative of this logo)
- Website design should incorporate the menu options shown in the attached PDF UI concept (UI does not necessarily need to look like the provided concept, just include all the clickable elements)
- Website design must portray an innovative and cooperative design environment with a look-and-feel that appeals to both amateur and professional designers.
- Please include pictures, illustrations and photographs (as needed) related to 3D printing, CAD design, conventional drafting, engineering and manufacturing industries.
- Design should support scaling to multiple screen sizes, from tablet computers (e.g. Zelo) to very large screen PCs.
- Design should include Username & Password fields for login or a button to pull up a login popup.
Nice to have
• - Website design could include "Invent", "Make", "Produce" and "Buy" options that slowly cycle through - with appropriate photos / graphics. These "menu options" would also be mouse-over enabled to switch into the appropriate context as the cursor enters that region (e.g. mouse over the "Invent" text would bring up page 2, etc.). (See attached Original UI Thoughts)
Should not have
• Requirements - Should Not Have:
- Website design should not portray a service that is very expensive or complicated - we are a reasonably priced service meant to be friendly with amateur inventors
- Website design should not be overly complicated - please keep it reasonably simple
- Website design should not be overly trendy
- Website design should not use more than 2 font styles, gaudy fonts, etc.
- Website design should not be "campy" or "tacky" - playful is ok, but please keep it elegant
- Website design should not be overly masculine or feminine - we will have both women and men as customers

```html
<!DOCTYPE html>
<html lang="en">
<head>
<meta charset="utf-8">
<title>Brindlecove Object Works, LLC – About B7</title>
<link href="https://fonts.googleapis.com/css2?family=Source+Sans+3:ital,wght@0,400;0,600;0,700;1,400&display=swap" rel="stylesheet">
<style>
:root{
  --ink:#222;
  --body:#444;
  --brand:#1f6aa5;
  --brand-light:#3a8fd2;
  --nav-dark:#0b4474;
  --nav-mid:#11598f;
  --orange:#f08a1c;
  --orange-light:#f9b233;
  --rule:#d6d6d6;
  --green:#3f9e2a;
  --button:#1d1d1d;
}
*{margin:0;padding:0;box-sizing:border-box}
html,body{width:1200px;height:1053px;overflow:hidden;background:#fff}
body{font-family:"Source Sans 3",Arial,sans-serif;color:var(--body);position:relative}
.abs{position:absolute}

.topbar{left:0;top:0;width:1200px;height:27px;background:linear-gradient(#3a3a3a,#1c1c1c)}
.topbar .links{left:321px;top:8px;display:flex;gap:18px;font-size:9px;color:#ddd;text-transform:uppercase}
.topbar .links .on{color:#fff;position:relative}
.topbar .links .on::after{content:"";position:absolute;left:11px;top:14px;border:5px solid transparent;border-bottom-color:var(--orange)}
.search-icon{left:553px;top:6px}
.search{left:574px;top:5px;width:181px;height:17px;background:#fff;border-radius:3px;font-size:7.5px;color:#999;padding:4px 7px}
.greeting{left:780px;top:8px;font-size:9px;color:#eee}
.greeting i{font-style:italic}

.header-bg{left:0;top:27px;width:1200px;height:160px;background:linear-gradient(#b9daf1,#e4f1fb 65%,#fff)}
.logo-mark{width:58px;height:64px;background:var(--brand)}
.brand-name{color:var(--brand);font-weight:400;white-space:nowrap}
.header .logo-mark{left:308px;top:44px}
.header .brand-name{left:374px;top:58px;font-size:26px}
.header .tagline{left:374px;top:87px;font-size:15px;color:var(--brand-light)}

.nav-shadow{left:210px;top:170px;width:780px;height:16px;border-radius:50%;background:radial-gradient(ellipse at center,rgba(120,140,160,.45),rgba(255,255,255,0) 70%)}
.nav{left:293px;top:138px;width:619px;height:45px;background:linear-gradient(var(--nav-mid),var(--nav-dark))}
.nav .home{left:0;top:0;width:53px;height:45px;background:linear-gradient(var(--orange-light),var(--orange))}
.nav .home-tip{left:53px;top:0}
.nav .home svg{position:absolute;left:12px;top:11px}
.nav .item{top:0;height:45px;padding-top:14px;color:#fff;font-size:10px;font-weight:600;text-transform:uppercase}
.nav .item small{display:block;font-size:7px;font-weight:400;color:#7fb0d8;text-transform:none;margin-top:1px}
.nav .item.active{left:61px;width:74px;background:#fff;color:var(--ink);border-top:3px solid var(--orange);padding-left:12px;padding-top:11px}
.nav .item.active small{color:#999}
.nav .divider{left:429px;top:0;width:1px;height:45px;background:#063152;box-shadow:1px 0 0 #2b6ea3}
.nav .cart-icon{left:441px;top:8px}
.nav .cart-label{left:479px;top:13px;font-size:8.5px;color:#fff;font-weight:600;line-height:10px}
.nav .cart-label span{color:var(--orange-light);font-weight:400}
.nav .shop-now{left:520px;top:9px;width:90px;height:28px;background:linear-gradient(#ffc43c,var(--orange));border:1px solid #c96a08;color:#3a2000;font-size:12px;font-weight:600;text-align:center;line-height:25px}

.crumb{left:300px;top:190px;font-size:8.5px;color:#555}
.crumb span{color:var(--orange)}
.rule{height:1px;background:var(--rule)}

.photo{background:linear-gradient(135deg,#8a7563,#c9b8a6 55%,#6e5844)}
.about-photo{left:300px;top:225px;width:245px;height:163px}
.h2{color:var(--ink);font-size:15px;font-weight:400}
.copy{font-size:8.4px;line-height:13px;color:var(--body)}
.about-title{left:561px;top:222px}
.about-copy{left:561px;top:249px;width:340px}
.about-copy p+p{margin-top:13px}

.why-title{left:300px;top:426px}
.why-sub{left:300px;top:445px;font-size:11px;color:var(--brand-light)}
.why-copy{left:300px;top:471px;width:604px}
.checks{top:532px;list-style:none}
.checks li{font-size:8.4px;height:19px;padding-left:14px;position:relative;line-height:12px}
.checks li::before{content:"";position:absolute;left:1px;top:2px;width:4px;height:7px;border:solid var(--green);border-width:0 2px 2px 0;transform:rotate(40deg)}

.section-shadow{left:420px;top:633px;width:375px;height:14px;background:radial-gradient(ellipse at top,rgba(0,0,0,.14),rgba(255,255,255,0) 70%);border-top:1px solid #ddd}

.product{top:653px;width:149px}
.product .thumb{height:90px;border:1px solid #d8d8d8;border-radius:2px;box-shadow:0 3px 4px rgba(0,0,0,.12)}
.product h3{font-size:11.5px;font-weight:400;color:var(--ink);margin-top:11px}
.product p{font-size:8.4px;line-height:11px;color:#555;margin-top:1px;width:110px}
.see-all{left:711px;top:827px;font-size:8.4px;color:#333}
.btn{background:var(--button);color:#fff;text-align:center;border-radius:2px;box-shadow:0 3px 3px rgba(0,0,0,.25)}
.find-more{left:812px;top:817px;width:81px;height:26px;font-size:11.5px;line-height:26px}

.footer .logo-mark{left:308px;top:886px}
.footer .brand-name{left:374px;top:890px;font-size:16.5px}
.footer .motto{left:374px;top:913px;font-size:12.5px;line-height:14px;color:var(--brand-light)}
.social{top:979px;width:24px;height:24px;border-radius:3px;background:linear-gradient(#dcdcdc,#a9a9a9);border:1px solid #999}
.social.on{background:linear-gradient(#555,#1c1c1c)}
.copyright{left:312px;top:1018px;font-size:7.5px;color:var(--brand)}
.foot-links{left:636px;top:887px;font-size:10px;color:var(--brand);font-weight:600;word-spacing:1px}
.foot-photo-frame{left:634px;top:918px;width:116px;height:52px;border:1px solid #ccc;padding:3px}
.foot-photo-frame div{width:100%;height:100%}
.foot-title{left:759px;top:916px;font-size:10px;color:var(--ink)}
.foot-copy{left:759px;top:935px;width:140px;font-size:7.8px;line-height:11px;color:#999}
.read-more{left:829px;top:974px;width:64px;height:26px;font-size:11px;line-height:26px}
</style>
</head>
<body>

<div class="abs topbar">
  <nav class="abs links"><span class="on">Why B7</span><span>Dreamer</span><span>Maker</span><span>Producer</span></nav>
  <svg class="abs search-icon" width="14" height="14" viewBox="0 0 14 14"><circle cx="8.5" cy="5.5" r="3.8" fill="none" stroke="#f08a1c" stroke-width="1.8"/><line x1="5.8" y1="8.2" x2="1.5" y2="12.5" stroke="#f08a1c" stroke-width="2.2"/></svg>
  <div class="abs search">Type search here...</div>
  <div class="abs greeting"><i>Hello Guest</i>, Login &nbsp;|&nbsp; Register</div>
</div>

<div class="abs header-bg"></div>
<header class="header">
  <div class="abs logo-mark"></div>
  <div class="abs brand-name">Brindlecove Object Works, LLC®</div>
  <div class="abs tagline">Shaping Your Ideas into Objects</div>
</header>

<div class="abs nav-shadow"></div>
<nav class="abs nav">
  <div class="abs home">
    <svg width="28" height="22" viewBox="0 0 28 22"><path d="M14 2 L2 12 H6 V21 H12 V15 H16 V21 H22 V12 H26 Z" fill="#fff"/></svg>
  </div>
  <svg class="abs home-tip" width="9" height="45"><path d="M0 0 L8 22.5 L0 45 Z" fill="#f08a1c"/></svg>
  <div class="abs item active">About B7<small>Nam liber temp</small></div>
  <div class="abs item" style="left:153px">Dream<small>Nobis eleifend</small></div>
  <div class="abs item" style="left:222px">Make<small>Dolor sit amet</small></div>
  <div class="abs item" style="left:285px">Produce<small>Adipiscing consec</small></div>
  <div class="abs item" style="left:364px">Sell<small>Ed delivero</small></div>
  <div class="abs divider"></div>
  <svg class="abs cart-icon" width="32" height="28" viewBox="0 0 32 28"><path d="M1 3 H6 L10 18 H26 L29 7 H8" fill="none" stroke="#dfe9f2" stroke-width="2"/><path d="M9 8 H28 L25.5 16 H11 Z" fill="#9fb9cf"/><circle cx="12" cy="23" r="2.4" fill="#dfe9f2"/><circle cx="24" cy="23" r="2.4" fill="#dfe9f2"/></svg>
  <div class="abs cart-label">Shopping<br>Chart <span>(0)</span></div>
  <div class="abs shop-now">Shopping NOW!</div>
</nav>

<div class="abs crumb">You at : <span>About B7</span></div>
<div class="abs rule" style="left:296px;top:203px;width:617px"></div>

<main>
  <div class="abs photo about-photo" role="img" aria-label="Photo of a 3D printed lattice high-heel shoe being worn"></div>
  <h1 class="abs h2 about-title">ABOUT B7</h1>
  <div class="abs copy about-copy">
    <p>Duis autem vel eum iriure dolor in hendrerit in vulputate velit esse molestie consequat, vel illum dolore eu feugiat nulla facilisis at vero eros et accumsan et iusto odio dignissim qui blandit praesent luptatum zzril delenit augue duis dolore te feugait nulla facilisi. Lorem ipsum dolor sit amet, consectetuer adipiscing elit, sed diam nonummy nibh euismod tincidunt ut laoreet dolore magna aliquam erat volutpat.</p>
    <p>Ut wisi enim ad minim veniam, quis nostrud exerci tation ullamcorper suscipit lobortis nisl ut aliquip ex ea commodo consequat. Duis autem vel eum iriure dolor in hendrerit in vulputate velit esse molestie consequat, vel illum dolore eu feugiat nulla facilisis at vero eros et accumsan et iusto odio dignissim qui blandit praesent luptatum zzril delenit augue</p>
  </div>

  <h2 class="abs h2 why-title">Why Choose Us?</h2>
  <div class="abs why-sub">Better choise</div>
  <p class="abs copy why-copy">Duis autem vel eum iriure dolor in hendrerit in vulputate velit esse molestie consequat, vel illum dolore eu feugiat nulla facilisis at vero eros et accumsan et iusto odio dignissim qui blandit praesent luptatum zzril delenit augue duis dolore te feugait nulla facilisi. Lorem ipsum dolor sit amet, consectetuer adipiscing elit, sed diam nonummy nibh euismod tincidunt ut laoreet dolore magna aliquam erat volutpat.</p>

  <ul class="abs checks" style="left:320px"><li>Nam liber tempor cum soluta.</li><li>Nobis eleifend option congue nihil.</li><li>Doming id quod mazim.</li><li>Lorem ipsum dolor sit amet.</li></ul>
  <ul class="abs checks" style="left:500px"><li>Nam liber tempor cum soluta.</li><li>Nobis eleifend option congue nihil.</li><li>Doming id quod mazim.</li><li>Lorem ipsum dolor sit amet.</li></ul>
  <ul class="abs checks" style="left:688px"><li>Nam liber tempor cum soluta.</li><li>Nobis eleifend option congue nihil.</li><li>Doming id quod mazim.</li><li>Lorem ipsum dolor sit amet.</li></ul>

  <div class="abs section-shadow"></div>

  <section>
    <article class="abs product" style="left:294px">
      <div class="thumb" role="img" aria-label="3D printed lattice ring product" style="background:radial-gradient(circle,#8a8a8a,#e9e9e9 55%,#fff)"></div>
      <h3>Product 1</h3><p>Nam liber tempor cum soluta nobis eleifend</p>
    </article>
    <article class="abs product" style="left:450px">
      <div class="thumb" role="img" aria-label="White printed mechanical part" style="background:radial-gradient(circle,#d8d6cc,#f4f4f1 55%,#fff)"></div>
      <h3>Product 1</h3><p>Nam liber tempor cum soluta nobis eleifend</p>
    </article>
    <article class="abs product" style="left:607px">
      <div class="thumb" role="img" aria-label="Assortment of colourful printed plastic parts" style="background:radial-gradient(circle,#d8602b,#4a4a4a 45%,#f2f2f2 75%)"></div>
      <h3>Product 1</h3><p>Nam liber tempor cum soluta nobis eleifend</p>
    </article>
    <article class="abs product" style="left:763px">
      <div class="thumb" role="img" aria-label="Printed wavy honeycomb structure in tan" style="background:linear-gradient(#e8d3b8,#b98f63 50%,#e6d0b3)"></div>
      <h3>Product 1</h3><p>Nam liber tempor cum soluta nobis eleifend</p>
    </article>
  </section>

  <div class="abs see-all">Please see our all product</div>
  <div class="abs btn find-more">Find out more!</div>
</main>

<div class="abs rule" style="left:247px;top:861px;width:714px"></div>

<footer class="footer">
  <div class="abs logo-mark"></div>
  <div class="abs brand-name">Brindlecove Object Works, LLC®</div>
  <div class="abs motto">What you want...<br>NOW!</div>
  <div class="abs social on" style="left:311px"></div>
  <div class="abs social" style="left:341px"></div>
  <div class="abs social" style="left:372px"></div>
  <div class="abs social" style="left:402px"></div>
  <div class="abs social" style="left:432px">
    <svg width="22" height="22" viewBox="0 0 22 22"><rect x="4" y="6" width="14" height="10" fill="none" stroke="#fff" stroke-width="1.3"/><path d="M4 6 L11 12 L18 6" fill="none" stroke="#fff" stroke-width="1.3"/></svg>
  </div>
  <div class="abs copyright">2012 © Copyright - Brindlecove Object Works, LLC</div>

  <nav class="abs foot-links">HOME &nbsp;|&nbsp; CONTACT &nbsp;|&nbsp; FRANCHISE &nbsp;|&nbsp; DISTRIBUTORS &nbsp;|&nbsp; CART</nav>
  <div class="abs foot-photo-frame"><div class="photo" role="img" aria-label="Photo of a 3D printed lattice shoe"></div></div>
  <div class="abs foot-title">At vero eos et accusam</div>
  <p class="abs foot-copy">Duis autem vel eum iriure dolor in hendrerit in vulputate velit esse molestie consequat.</p>
  <div class="abs btn read-more">Read more</div>
</footer>

</body>
</html>
```